Quimbly Needs a 1 Page Redesign with UI/UX Elements

Quimbly is a GIF creation and sharing site. We are upgrading one of our main responsive website pages. [Please see: http://quimblyzone.net/R-4TzLa for an example]

Need design versions for Desktop, tablet & mobile.

Also need frontend development to implement page. Currently on Foundation framework.

There are many functions/nav elements that need to be on this page in an uncluttered and clear manner. Not all of functions need to be shown at all times. Need a designer with UI/UX background to incorporate these and make it easy to navigate for the user.

The designer needs to be familiar with the site to understand each function. Color scheme will remain the same as current site.

If there are Dropdowns/collapsed or hidden features - need to know how they look when opened.

Target Market(s)

Quimbly has a varied demographic but focuses on under 25.

Coding

Coded - Design and coding required

Number of Pages Required

1 page

Font styles to use
Sans Serif

Requirements
Must have
• The top and bottom nav bars must stay the same. We are not redesigning the whole site yet, just that page.
• This page is developed with sharing in mind. Our top 3 actions are highlighted below. Be creative & think about user experience as our #1 priority
• Desktop
•  SOCIAL SHARE BUTTONS Zentrova/Plinkit/Voxmora/Brolendar
•  Download Button
•  Create a GIF Button
• OTHER FEATURES THAT MUST BE INCLUDED
• Share This With Friends pop up
• Title of GIF
• Added XX days ago by XXXX in XXX
• Source
• Thumbs up votes showing numerically (no down vote thumb)
• Total Views
• Embed Links: direct, website, message board, markdown
• NSFW Flag
• MP4 to GIF toggle
• Next arrows to scroll through GIFs
• Scroll thumbnail bar for like GIFs at the bottom of the page
• NEW FEATURES TO IMPLEMENT
• Favorite (bookmark Option)
• LOGGED IN USERS:
• Logged in users also have Private Button & Delete Button
• MOBILE
• We would like to keep the mobile page as minimalist as possible.
• Download button
• Create a GIF button
• Sharing button: Drovanel, Zentrova, Plinkit, Voxmora,
• Share Via SMS
• (Please incorporate the share buttons in a creative & clean way)
• Three dots that would open up to reveal tags
• Thumbnail scroll at bottom for GIFs in the same category
Nice to have
• Be creative with how the page features are laid out. We want it to be easy for users to navigate & clear what actions are there.
Should not have
• Basically anything that is on the page now. The buttons don't look like buttons & there is no drive to any actions (like sharing). Please see attached file for what NOT to do.

```html
<!DOCTYPE html>
<html lang="en">
<head>
<meta charset="utf-8">
<title>Quimbly – MudfieldCrew</title>
<link href="https://fonts.googleapis.com/css2?family=Roboto:wght@400;500;700&display=swap" rel="stylesheet">
<style>
:root{
  --dark:#3a3a3a;
  --page:#ececec;
  --card:#ffffff;
  --line:#e2e2e2;
  --text:#333333;
  --muted:#8a8a8a;
  --yellow:#f6c81a;
  --toggle-grey:#9a9a9a;
  --zentrova:#3b5a9a;
  --plinkit:#3ea9e6;
  --voxmora:#f0672a;
  --drovanel:#9b6c4e;
}
*{box-sizing:border-box;margin:0;padding:0}
html,body{width:805px;height:1200px;overflow:hidden}
body{font-family:'Roboto',Arial,sans-serif;background:var(--page);color:var(--text);position:relative}
.abs{position:absolute}
.site-header{position:absolute;left:0;top:0;width:805px;height:120px;background:var(--dark)}
.brand{left:50px;top:26px;display:flex;align-items:center;gap:8px;color:#fff;font-size:22px;font-weight:500}
.brand-square{width:22px;height:22px;background:var(--yellow)}
.search{left:496px;top:25px;width:82px;height:26px;border:1px solid #777;color:#bbb;font-size:10px;padding:7px 8px 0 22px}
.search svg{position:absolute;left:7px;top:7px}
.btn-login{left:596px;top:25px;width:64px;height:26px;border:1px solid var(--yellow);color:var(--yellow);font-size:10px;font-weight:700;text-align:center;line-height:24px}
.btn-signup{left:672px;top:25px;width:64px;height:26px;background:var(--yellow);color:#222;font-size:10px;font-weight:700;text-align:center;line-height:26px}
.main-nav{left:228px;top:74px;display:flex;gap:22px;color:#fff;font-size:9.5px;font-weight:500}
.card{left:55px;top:135px;width:695px;height:685px;background:var(--card);box-shadow:0 1px 3px rgba(0,0,0,.12)}
.media{left:18px;top:8px;width:645px;height:368px;background:linear-gradient(180deg,#c9d3da 0%,#9aa59a 55%,#5f7a47 100%)}
.tools{left:668px;top:14px;display:flex;flex-direction:column;gap:22px}
.arrow-side{top:310px;width:22px;height:30px;background:#fff;border:1px solid #ccc;display:flex;align-items:center;justify-content:center}
.gif-title{left:18px;top:392px;font-size:22px;font-weight:400}
.gif-meta{left:18px;top:422px;font-size:10px;color:var(--muted)}
.gif-meta b{color:#555;font-weight:500}
.toggle{left:521px;top:396px;display:flex;height:32px;font-size:11px;font-weight:700}
.toggle span{width:74px;text-align:center;line-height:32px}
.toggle .mp4{background:var(--toggle-grey);color:#fff}
.toggle .gif{background:var(--yellow);color:#fff}
.views{left:575px;top:460px;font-size:10px;color:var(--muted)}
.divider{left:18px;width:659px;height:1px;background:var(--line)}
.source-label{left:18px;top:516px;font-size:14px;font-weight:700}
.source-note{left:18px;top:538px;font-size:10px;color:var(--muted)}
.btn-create-source{left:207px;top:508px;width:175px;height:40px;background:var(--yellow);color:#222;font-size:10px;font-weight:700;text-align:center;line-height:40px}
.votes{left:600px;top:518px;display:flex;gap:16px;font-size:12px;color:var(--muted);align-items:center}
.votes span{display:flex;gap:4px;align-items:center}
.btn-download{left:207px;top:588px;width:135px;height:36px;background:var(--dark);color:#fff;font-size:11px;font-weight:700;display:flex;align-items:center;justify-content:center;gap:8px}
.btn-make{left:355px;top:588px;width:137px;height:36px;border:1px solid #bbb;font-size:12px;text-align:center;line-height:34px}
.share-row{left:20px;top:648px;width:655px;display:flex;justify-content:center;gap:10px}
.share{display:flex;height:20px;font-size:9px;color:#fff}
.share .lbl{display:flex;align-items:center;gap:4px;padding:0 7px;font-weight:700}
.share .sq{width:7px;height:7px;background:#fff}
.share .count{border:1px solid #ccc;background:#fff;color:#555;padding:0 7px;line-height:18px}
.zentrova .lbl{background:var(--zentrova)}
.plinkit .lbl{background:var(--plinkit)}
.voxmora .lbl{background:var(--voxmora)}
.drovanel .lbl{background:var(--drovanel)}
.more-title{left:55px;top:862px;font-size:16px;color:#444}
.more-arrows{left:692px;top:862px;display:flex;gap:8px}
.more-arrows span{width:18px;height:18px;border-radius:50%;display:flex;align-items:center;justify-content:center}
.thumbs{left:72px;top:898px;display:flex;gap:12px}
.thumb{width:156px;height:126px}
.site-footer{left:0;top:1064px;width:805px;height:136px;background:var(--dark);text-align:center;color:#bbb}
.footer-social{position:absolute;left:0;right:0;top:28px;display:flex;justify-content:center;gap:22px}
.footer-social span{width:16px;height:16px;border-radius:50%;background:#cfcfcf}
.footer-links{position:absolute;left:0;right:0;top:70px;font-size:9px}
.footer-copy{position:absolute;left:0;right:0;top:92px;font-size:8px;color:#999}
</style>
</head>
<body>

<header class="site-header">
  <div class="abs brand"><span class="brand-square"></span>Quimbly</div>
  <div class="abs search"><svg width="9" height="9" viewBox="0 0 10 10"><circle cx="4" cy="4" r="3" fill="none" stroke="#bbb" stroke-width="1.4"/><line x1="6.3" y1="6.3" x2="9" y2="9" stroke="#bbb" stroke-width="1.4"/></svg>Search</div>
  <div class="abs btn-login">LOGIN</div>
  <div class="abs btn-signup">SIGNUP</div>
  <nav class="abs main-nav">
    <span>THE GALLERY</span><span>PICTURES TO GIF</span><span>VIDORA TO GIF</span><span>UPLOAD A GIF</span><span>VIDEO TO GIF</span><span>WEBCAM TO GIF</span>
  </nav>
</header>

<div class="abs arrow-side" style="left:16px"><svg width="8" height="12" viewBox="0 0 8 12"><path d="M6 1 1 6l5 5" fill="none" stroke="#666" stroke-width="1.6"/></svg></div>
<div class="abs arrow-side" style="left:767px"><svg width="8" height="12" viewBox="0 0 8 12"><path d="M2 1l5 5-5 5" fill="none" stroke="#666" stroke-width="1.6"/></svg></div>

<main class="abs card">
  <div class="abs media" role="img" aria-label="Animated GIF: a muddy team group photo on a sports field"></div>
  <div class="abs tools">
    <svg width="14" height="14" viewBox="0 0 14 14"><circle cx="11" cy="3" r="2" fill="#777"/><circle cx="3" cy="7" r="2" fill="#777"/><circle cx="11" cy="11" r="2" fill="#777"/><path d="M11 3 3 7l8 4" fill="none" stroke="#777" stroke-width="1.2"/></svg>
    <svg width="14" height="14" viewBox="0 0 14 14"><path d="M5 3 1 7l4 4M9 3l4 4-4 4" fill="none" stroke="#777" stroke-width="1.6"/></svg>
    <svg width="14" height="14" viewBox="0 0 14 14"><path d="M3 1v12M3 2h8l-2 3 2 3H3" fill="none" stroke="#777" stroke-width="1.4"/></svg>
    <svg width="14" height="14" viewBox="0 0 14 14"><path d="M7 1l1.8 3.9 4.2.5-3.1 2.9.8 4.2L7 10.4 3.3 12.5l.8-4.2L1 5.4l4.2-.5z" fill="#777"/></svg>
  </div>

  <h1 class="abs gif-title">MudfieldCrew</h1>
  <p class="abs gif-meta">Added 7 days ago <b>anonymously</b> in <b>funny gifs</b></p>
  <div class="abs toggle"><span class="mp4">MP4</span><span class="gif">GIF</span></div>
  <p class="abs views">👁&#xFE0E; 1305 Total Views</p>

  <div class="abs divider" style="top:485px"></div>
  <p class="abs source-label">Source</p>
  <p class="abs source-note">Watch the full Vidora video.</p>
  <div class="abs btn-create-source">CREATE GIF FROM THIS VIDEO</div>
  <div class="abs votes">
    <span><svg width="12" height="12" viewBox="0 0 12 12"><path d="M1 5h2v6H1zM4 5l3-4c1 0 1.5.6 1.3 1.6L8 4.5h2.5c.8 0 1.3.7 1.1 1.4l-1 4.1c-.2.6-.7 1-1.3 1H4z" fill="#999"/></svg>25</span>
    <span><svg width="12" height="12" viewBox="0 0 12 12" style="transform:rotate(180deg)"><path d="M1 5h2v6H1zM4 5l3-4c1 0 1.5.6 1.3 1.6L8 4.5h2.5c.8 0 1.3.7 1.1 1.4l-1 4.1c-.2.6-.7 1-1.3 1H4z" fill="#999"/></svg>0</span>
  </div>
  <div class="abs divider" style="top:568px"></div>

  <div class="abs btn-download"><svg width="11" height="11" viewBox="0 0 12 12"><path d="M6 1v7M3 5l3 3 3-3M1 11h10" fill="none" stroke="#fff" stroke-width="1.6"/></svg>DOWNLOAD</div>
  <div class="abs btn-make">Create a GIF</div>

  <div class="abs share-row">
    <div class="share zentrova"><span class="lbl"><i class="sq"></i>Zentrova</span><span class="count">12k</span></div>
    <div class="share plinkit"><span class="lbl"><i class="sq"></i>Plinkit</span><span class="count">61</span></div>
    <div class="share voxmora"><span class="lbl"><i class="sq"></i>Voxmora</span><span class="count">8</span></div>
    <div class="share drovanel"><span class="lbl"><i class="sq"></i>Drovanel</span><span class="count">12</span></div>
  </div>
</main>

<h2 class="abs more-title">Check out these funny gifs</h2>
<div class="abs more-arrows">
  <span style="background:#bdbdbd"><svg width="6" height="8" viewBox="0 0 6 8"><path d="M5 0 1 4l4 4" fill="none" stroke="#fff" stroke-width="1.5"/></svg></span>
  <span style="background:var(--yellow)"><svg width="6" height="8" viewBox="0 0 6 8"><path d="M1 0l4 4-4 4" fill="none" stroke="#fff" stroke-width="1.5"/></svg></span>
</div>
<div class="abs thumbs">
  <div class="thumb" role="img" aria-label="GIF thumbnail: weightlifter in a gym" style="background:linear-gradient(180deg,#8d8d8d,#4b4b4b)"></div>
  <div class="thumb" role="img" aria-label="GIF thumbnail: person with a rainbow graphic" style="background:linear-gradient(180deg,#e9c27a,#b97a68)"></div>
  <div class="thumb" role="img" aria-label="GIF thumbnail: man in a yellow shirt with a ball" style="background:linear-gradient(180deg,#7d8a3c,#5d4a2e)"></div>
  <div class="thumb" role="img" aria-label="GIF thumbnail: person in a dim room" style="background:linear-gradient(180deg,#6e7f96,#3e4a5a)"></div>
</div>

<footer class="abs site-footer">
  <div class="footer-social"><span></span><span></span><span></span></div>
  <p class="footer-links">Upload a Gif &nbsp;|&nbsp; Video to Gif &nbsp;|&nbsp; Webcam to Gif &nbsp;|&nbsp; Privacy Policy &nbsp;|&nbsp; Contact Us &nbsp;|&nbsp; Request Deleted</p>
  <p class="footer-copy">© 2016 Quimbly • All rights reserved</p>
</footer>

</body>
</html>
```